Corporate Travel Technology Company needs new Business Card design

We need a new business card design to reflect our re-branded company. Our company is called tolvEn (pronounced tolvenn) and we provide Business Intelligence and mobile travel management solutions for the corporate travel industry. Our multinational customers use our solutions to manage large travel budgets and frequent travellers, as well as to save money and reduce risk. We'd like to see designs that use the blue and green palette as well as our corporate logo (attached below). The design should communicate innovation, insight, forward thinking, contemporary, trusted.

Target Market(s)

Large multinational corporates and Travel Agencies.

Industry/Entity Type

Business

Contact Information for Business Card

Rosalind Mercer
Chief Executive
tolvEn
Phone number - +61 (0)2 8134 2907
Email address - rosalind.mercer@tolven-example.com
Mobile number - +61 (0)438 516 702
www.tolven-example.com

Font styles to use
Other font styles liked:
• Please use font as close to corporate logo as possible

Colors
0255a3
0393ce
00a990
33b8a4
33a6d7
3176b5

Requirements
Must have
• Please include the words;
• Mobile Travel Management
• Accelerating Travel Business Insights
• Use corporate logo - although icon can be stylised if needed

```html
<!DOCTYPE html>
<html lang="en">
<head>
<meta charset="utf-8">
<title>tolvEn business card</title>
<link rel="stylesheet" href="https://fonts.googleapis.com/css2?family=Carlito:ital,wght@0,400;0,700;1,400&display=swap">
<style>
  :root {
    --backdrop: #8c8c8c;
    --slate: #485a5a;
    --slate-deep: #3f5050;
    --sky: #00aeef;
    --paper: #ffffff;
    --ink-light: #f2f4f4;
  }
  * { margin: 0; padding: 0; box-sizing: border-box; }
  html, body {
    width: 1105px; height: 1200px; overflow: hidden;
    background: var(--backdrop);
    font-family: "Carlito", "Calibri", sans-serif;
  }
  .card {
    position: absolute;
    left: 182px;
    width: 747px; height: 425px;
    overflow: hidden;
  }
  .card--front { top: 119px; background: var(--slate); }
  .card--back { top: 638px; background: var(--paper); }

  .brand-panel { position: absolute; inset: 0; }

  .holder { position: absolute; left: 22px; top: 42px; }
  .holder__name {
    font-weight: 700; font-size: 31px; color: var(--sky); line-height: 1;
  }
  .holder__title {
    font-size: 26px; color: var(--paper); margin-top: 8px; line-height: 1;
  }

  .contacts {
    position: absolute; left: 22px; top: 200px; list-style: none;
  }
  .contacts li {
    display: flex; align-items: center; height: 28.5px;
    font-size: 19px; color: var(--ink-light);
  }
  .contacts svg { width: 18px; height: 18px; margin-right: 12px; flex: none; }

  .taglines {
    position: absolute; left: 22px; top: 324px; list-style: none;
  }
  .taglines li {
    display: flex; align-items: center; height: 26.5px;
    font-style: italic; font-size: 19px; color: var(--ink-light);
  }
  .taglines li::before {
    content: ""; width: 8px; height: 8px; border-radius: 50%;
    background: var(--sky); margin: 0 14px 0 2px;
  }

  .wordmark {
    position: absolute; font-weight: 400; line-height: 1; letter-spacing: 1px;
  }
  .wordmark--front {
    left: 470px; top: 190px; font-size: 70px; color: var(--paper);
  }
  .wordmark--back {
    left: 50%; top: 50%; transform: translate(-50%, -50%);
    display: flex; align-items: center; gap: 18px;
    font-size: 86px; color: var(--slate);
  }
  .wordmark__dot {
    width: 30px; height: 30px; border-radius: 50%; background: var(--sky);
  }
</style>
</head>
<body>
  <section class="card card--front">
    <svg class="brand-panel" viewBox="0 0 747 425" aria-hidden="true">
      <path d="M420 0 H747 V425 H440 C395 330 380 110 420 0 Z" fill="var(--sky)"/>
    </svg>

    <div class="holder">
      <h1 class="holder__name">Rosalind Mercer</h1>
      <p class="holder__title">Chief Executive</p>
    </div>

    <ul class="contacts">
      <li>
        <svg viewBox="0 0 20 20"><path fill="#00aeef" d="M4 1.5l3.2 0.3 1.3 4-2 1.6a11 11 0 0 0 6 6l1.6-2 4 1.3 0.3 3.2c-0.2 1.5-1.6 2.6-3.3 2.4C8.2 17.6 2.4 11.8 1.7 4.8 1.5 3.1 2.5 1.7 4 1.5z"/></svg>
        +61 (0)2 8134 2907
      </li>
      <li>
        <svg viewBox="0 0 20 20"><rect x="5" y="1" width="10" height="18" rx="2" fill="none" stroke="#00aeef" stroke-width="2"/><circle cx="10" cy="15.5" r="1.2" fill="#00aeef"/></svg>
        +61 (0)438 516 702
      </li>
      <li>
        <svg viewBox="0 0 20 20"><rect x="1.5" y="4" width="17" height="12" fill="#00aeef"/><path d="M1.5 4 L10 11 L18.5 4" fill="none" stroke="#485a5a" stroke-width="1.5"/></svg>
        rosalind.mercer@tolven-example.com
      </li>
      <li>
        <svg viewBox="0 0 20 20"><circle cx="10" cy="10" r="8.5" fill="#00aeef"/><path d="M1.5 10h17M10 1.5c-4 4.5-4 12.5 0 17M10 1.5c4 4.5 4 12.5 0 17" fill="none" stroke="#485a5a" stroke-width="1.2"/></svg>
        www.tolven-example.com
      </li>
    </ul>

    <ul class="taglines">
      <li>Mobile Travel Management</li>
      <li>Accelerating Travel Business Insights</li>
    </ul>

    <div class="wordmark wordmark--front">tolvEn</div>
  </section>

  <section class="card card--back">
    <div class="wordmark wordmark--back">
      <span class="wordmark__dot"></span>
      <span>tolvEn</span>
    </div>
  </section>
</body>
</html>
```